Product Designer Business Card

Small product design, engineering and prototyping firm in need of a clean, professional business card design. To support our 3D design and drawing services, we offer 3D printing, molding, and casting of plastics, silicones, resins, etc. Our logo can still be modified/changed if necessary. The red/orange color is preferred, but may be substituted with blue or green, potentially. Either way, the colour of the logo should be match/compliment colors used throughout the design. One thought is to have the logo/contact info on one side, with the other side describing services offered, like with a small icon of 3D printer, molding, casting, and computer with a 3D model on-screen.
Industry/Entity Type
Mechanical Engineering
Contact Information for Business Card
Company: Kelvar Design
Phone: 613-582-9047
Email: mark@kelvardesign.ca

```html
<!DOCTYPE html>
<html lang="en">
<head>
<meta charset="utf-8">
<title>Kelvar Design — Business Card</title>
<link href="https://fonts.googleapis.com/css2?family=Exo+2:wght@400;500;700&display=swap" rel="stylesheet">
<style>
  :root {
    --bg: #e9e9e9;
    --ink-dark: #1f1f1f;
    --ink-text: #2a2a2a;
    --red: #e0260c;
    --red-deep: #7c1207;
    --red-mid: #b81b09;
    --paper: #ffffff;
  }
  html, body {
    margin: 0;
    width: 1200px;
    height: 1015px;
    overflow: hidden;
    background: var(--bg);
    font-family: "Exo 2", sans-serif;
  }
  .canvas { position: relative; width: 1200px; height: 1015px; }
  .card {
    position: absolute;
    left: 280px;
    width: 640px;
    height: 366px;
    box-shadow: 0 14px 30px rgba(0,0,0,0.25);
    overflow: hidden;
  }
  .card--back { top: 90px; }
  .card--front { top: 560px; }
  .card-bg { position: absolute; inset: 0; }

  .brand-name {
    position: absolute;
    margin: 0;
    color: var(--red);
    font-weight: 500;
    letter-spacing: 1px;
    line-height: 1;
    white-space: nowrap;
  }
  .card--back .brand-name { left: 52px; top: 164px; font-size: 40px; }
  .card--front .brand-name { left: 52px; top: 104px; font-size: 42px; }

  .services {
    position: absolute;
    left: 385px; top: 62px;
    display: grid;
    grid-template-columns: 120px 120px;
    row-gap: 34px;
    column-gap: 10px;
  }
  .service { text-align: center; color: var(--paper); font-size: 15px; }
  .service svg { display: block; margin: 0 auto 6px; }

  .contact {
    position: absolute;
    left: 56px; top: 252px;
    list-style: none; margin: 0; padding: 0;
    color: var(--ink-text);
    font-size: 19px;
  }
  .contact li { display: flex; align-items: center; gap: 10px; height: 28px; }
  .contact svg { flex: none; }

  .nameplate {
    position: absolute;
    left: 400px; top: 158px;
    color: var(--paper);
  }
  .person-name { font-size: 27px; font-weight: 700; line-height: 1.1; }
  .person-title { font-size: 17px; font-weight: 500; padding-left: 30px; }
</style>
</head>
<body>
<main class="canvas">

  <section class="card card--back" aria-label="Card back with services">
    <svg class="card-bg" width="640" height="366" viewBox="0 0 640 366">
      <defs>
        <linearGradient id="backRed" x1="0" y1="0" x2="0" y2="1">
          <stop offset="0" stop-color="var(--red-deep)"/>
          <stop offset="1" stop-color="var(--red)"/>
        </linearGradient>
      </defs>
      <rect width="640" height="366" fill="var(--ink-dark)"/>
      <polygon points="340,0 640,0 640,366 412,366" fill="url(#backRed)"/>
    </svg>

    <p class="brand-name">Kelvar Design</p>

    <div class="services">
      <div class="service">
        <svg width="76" height="62" viewBox="0 0 76 62" fill="none" stroke="#fff" stroke-width="4">
          <rect x="4" y="4" width="68" height="54" rx="4"/>
          <path d="M18 46 H58 M24 46 V34 H52 V46 M30 34 V18 H40 V34" stroke-width="3"/>
        </svg>Casting
      </div>
      <div class="service">
        <svg width="76" height="62" viewBox="0 0 76 62" fill="none" stroke="#fff" stroke-width="4">
          <rect x="4" y="4" width="68" height="54" rx="4"/>
          <rect x="16" y="14" width="44" height="28" stroke-width="3"/>
          <path d="M38 42 V50 M28 50 H48" stroke-width="3"/>
          <circle cx="38" cy="28" r="7" stroke-width="3"/>
        </svg>3d Model
      </div>
      <div class="service">
        <svg width="76" height="62" viewBox="0 0 76 62" fill="none" stroke="#fff" stroke-width="4">
          <rect x="4" y="4" width="68" height="54" rx="4"/>
          <rect x="16" y="14" width="44" height="32" stroke-width="3"/>
          <path d="M16 22 H60 M30 22 V30 H46 V22 M24 40 H52" stroke-width="3"/>
        </svg>3D Printer
      </div>
      <div class="service">
        <svg width="76" height="62" viewBox="0 0 76 62" fill="none" stroke="#fff" stroke-width="4">
          <rect x="4" y="4" width="68" height="54" rx="4"/>
          <path d="M20 14 H56 V22 H20 Z M28 22 V32 H48 V22 M20 40 H56 V48 H20 Z" stroke-width="3"/>
        </svg>Molding
      </div>
    </div>
  </section>

  <section class="card card--front" aria-label="Card front with contact details">
    <svg class="card-bg" width="640" height="366" viewBox="0 0 640 366">
      <defs>
        <linearGradient id="bandRed" x1="0" y1="0" x2="1" y2="0">
          <stop offset="0" stop-color="var(--red-mid)"/>
          <stop offset="1" stop-color="var(--red)"/>
        </linearGradient>
      </defs>
      <rect width="640" height="366" fill="var(--ink-dark)"/>
      <polygon points="0,0 398,0 474,366 0,366" fill="var(--paper)"/>
      <polygon points="380,150 640,150 640,218 380,218" fill="url(#bandRed)"/>
      <polygon points="396,218 440,218 426,236" fill="var(--red-deep)"/>
    </svg>

    <p class="brand-name">Kelvar Design</p>

    <div class="nameplate">
      <div class="person-name">Tobias Renner</div>
      <div class="person-title">Managing Director</div>
    </div>

    <ul class="contact">
      <li>
        <svg width="18" height="18" viewBox="0 0 18 18" fill="none" stroke="var(--red)" stroke-width="2">
          <rect x="1" y="1" width="16" height="16" rx="2"/>
          <path d="M5 5 C5 10 8 13 13 13 L13 11 L10.5 10 L9.5 11 C8 10.5 7.5 10 7 8.5 L8 7.5 L7 5 Z" fill="var(--red)" stroke="none"/>
        </svg>613-582-9047
      </li>
      <li>
        <svg width="18" height="14" viewBox="0 0 18 14">
          <rect x="0" y="0" width="18" height="14" fill="var(--red)"/>
          <path d="M1 1 L9 8 L17 1" fill="none" stroke="#fff" stroke-width="1.6"/>
        </svg>mark@kelvardesign.ca
      </li>
      <li>
        <svg width="18" height="18" viewBox="0 0 18 18" fill="none" stroke="var(--red)" stroke-width="1.8">
          <circle cx="9" cy="9" r="8"/>
          <ellipse cx="9" cy="9" rx="3.5" ry="8"/>
          <path d="M1 9 H17 M2.5 5 H15.5 M2.5 13 H15.5"/>
        </svg>www.kelvardesign.ca
      </li>
    </ul>
  </section>

</main>
</body>
</html>
```